Kelvor Engineers: Why you should hire us keepsake

New design. Open to plastic cards. We are an engineering firm that designs cell phone towers and commercial buildings. Please check out our website www.kelvorstruct.com for more details. We want people to remember our card and for it to be useful if possible. We want the same look and feel on these cards to be translated to other marketing material we may need such as brochures.

Target Market(s)

Architects, Developers and Telecommunication Carriers

Industry/Entity Type

Engineering

Contact Information for Business Card

Card with our company colors, logo, and innovative design with elements related to our industry.

Font styles to use
Sans Serif

Colors
9bcb3c
abd036
0255a3

Requirements
Must have
• Sleek and hip design
Nice to have
• Bright lime green and navy coloring that pops with an innovative design.
Should not have
• A basic and boring design

```html
<!DOCTYPE html>
<html lang="en">
<head>
<meta charset="utf-8">
<title>Kelvor Engineers — Business Card</title>
<link rel="stylesheet" href="https://fonts.googleapis.com/css2?family=Work+Sans:wght@400;500;700;800&display=swap">
<style>
  :root {
    --navy: #1d3461;
    --lime: #c8d42a;
    --white: #ffffff;
    --stage: #3a3a3c;
  }
  * { box-sizing: border-box; margin: 0; padding: 0; }
  html, body { width: 1200px; height: 900px; overflow: hidden; }
  body {
    background: var(--stage);
    font-family: "Work Sans", Arial, sans-serif;
    position: relative;
  }
  .card {
    position: absolute;
    width: 560px;
    height: 320px;
    border-radius: 22px;
    overflow: hidden;
    box-shadow: 0 10px 30px rgba(0,0,0,.35);
  }
  /* Back of card */
  .card--back { left: 460px; top: 70px; background: var(--navy); }
  .card--back .wordmark {
    position: absolute;
    right: 50px; top: 92px;
    color: var(--lime);
    font-weight: 800;
    font-size: 52px;
    line-height: 1;
    letter-spacing: -1px;
    text-align: right;
  }
  .card--back .wordmark span { display: block; }
  .cities {
    position: absolute;
    left: 40px; right: 40px; bottom: 34px;
    color: var(--white);
    font-weight: 500;
    font-size: 15px;
    letter-spacing: 1.6px;
    text-transform: uppercase;
    text-align: center;
    white-space: nowrap;
  }
  .cities .sep { color: var(--lime); margin: 0 6px; }

  /* Front of card */
  .card--front { left: 180px; top: 480px; background: var(--white); }
  .card--front .wave { position: absolute; left: 0; top: 0; width: 560px; height: 320px; }
  .card--front .wordmark {
    position: absolute;
    right: 40px; top: 34px;
    color: var(--lime);
    font-weight: 800;
    font-size: 40px;
    line-height: 1;
    letter-spacing: -1px;
    text-align: right;
  }
  .card--front .wordmark span { display: block; }
  .person {
    position: absolute;
    right: 40px; top: 132px;
    text-align: right;
  }
  .person .name { color: var(--navy); font-weight: 700; font-size: 19px; }
  .person .role { color: var(--lime); font-weight: 400; font-size: 15px; margin-top: 2px; }
  .contacts {
    position: absolute;
    right: 40px; top: 186px;
    list-style: none;
    color: var(--navy);
    font-size: 14px;
    line-height: 19px;
  }
  .contacts li { display: flex; justify-content: flex-end; align-items: center; gap: 8px; }
  .contacts svg { width: 11px; height: 11px; fill: none; stroke: var(--lime); stroke-width: 1.6; }
  .tagline {
    position: absolute;
    left: 58px; bottom: 18px;
    color: var(--navy);
    font-size: 18px;
    letter-spacing: 5px;
    text-transform: uppercase;
    white-space: nowrap;
  }
</style>
</head>
<body>

<section class="card card--back" aria-label="Card back">
  <div class="wordmark"><span>Kelvor</span><span>Engineers</span></div>
  <p class="cities">Denver<span class="sep">/</span>Raleigh<span class="sep">/</span>Phoenix<span class="sep">/</span>Tulsa</p>
</section>

<section class="card card--front" aria-label="Card front">
  <svg class="wave" viewBox="0 0 560 320" aria-hidden="true">
    <path fill="var(--navy)" d="M0 0 H140 C136 95 70 150 48 225 C38 260 34 295 34 320 H0 Z"/>
    <path fill="var(--lime)" d="M140 0 H154 C152 100 86 158 64 228 C54 262 48 295 46 320 H34 C34 295 38 260 48 225 C70 150 136 95 140 0 Z"/>
    <path fill="none" stroke="var(--white)" stroke-width="2" d="M124 0 C118 90 56 145 34 240"/>
  </svg>

  <div class="wordmark"><span>Kelvor</span><span>Engineers</span></div>

  <div class="person">
    <p class="name">Dana Whitlock Mercer</p>
    <p class="role">Director</p>
  </div>

  <ul class="contacts">
    <li>555.014.7310
      <svg viewBox="0 0 12 12"><path d="M3 1 L5 3.5 L4 5 Q5.5 7.5 7 8 L8.5 7 L11 9 L9.5 11 Q4 10 1 3 Z"/></svg></li>
    <li>555.019.4826
      <svg viewBox="0 0 12 12"><rect x="3" y="1" width="6" height="10" rx="1"/><line x1="5.5" y1="9" x2="6.5" y2="9"/></svg></li>
    <li>dmercer@kelvorstruct.com
      <svg viewBox="0 0 12 12"><rect x="1" y="2.5" width="10" height="7"/><path d="M1 2.5 L6 6.5 L11 2.5"/></svg></li>
    <li>www.kelvorstruct.com
      <svg viewBox="0 0 12 12"><circle cx="6" cy="6" r="5"/><ellipse cx="6" cy="6" rx="2" ry="5"/><line x1="1" y1="6" x2="11" y2="6"/></svg></li>
  </ul>

  <p class="tagline">Multi-Discipline Engineering</p>
</section>

</body>
</html>
```